Redesign of business card for Cedar Ridge Mechanical

We are looking for a new design for our business cards for Cedar Ridge Mechanical. We are a plumbing & HVAC construction company, operating on the West Coast of Canada and USA. Logo attached.
Industry/Entity Type
Construction - Plumbing & HVAC
Contact Information for Business Card
Name, address, phone numbers, email, website address
Look and feel
Each slider illustrates characteristics of the customer's brand and the style your logo design should communicate.

```html
<!DOCTYPE html>
<html lang="en">
<head>
<meta charset="utf-8">
<title>Cedar Ridge Mechanical – Business Cards</title>
<link href="https://fonts.googleapis.com/css2?family=Open+Sans:wght@400;600;700&display=swap" rel="stylesheet">
<style>
  :root {
    --backdrop: #222222;
    --card-white: #ffffff;
    --ink: #111111;
    --ink-muted: #6a6a6a;
  }
  * { box-sizing: border-box; margin: 0; padding: 0; }
  html, body {
    width: 1200px; height: 780px; overflow: hidden;
    background: var(--backdrop);
    font-family: "Open Sans", Arial, sans-serif;
  }
  .sheet {
    position: relative; width: 1200px; height: 780px;
    display: flex; align-items: center; justify-content: center; gap: 60px;
  }
  .card {
    position: relative; width: 520px; height: 300px;
    background: var(--card-white); overflow: hidden;
  }
  .card-contact .swoosh { position: absolute; inset: 0; }
  .holder { position: absolute; left: 34px; top: 34px; color: var(--ink); }
  .holder-name { font-weight: 700; font-size: 17px; letter-spacing: .3px; }
  .holder-title { font-size: 12px; color: var(--ink-muted); margin-top: 1px; }
  .title-rule {
    position: absolute; left: 170px; top: 94px; width: 130px;
    border-top: 1px solid var(--ink);
  }
  .contact-list { position: absolute; left: 34px; top: 96px; list-style: none; }
  .contact-list li {
    display: flex; align-items: center; gap: 6px;
    font-size: 13px; color: var(--ink); line-height: 21px;
  }
  .contact-list svg { width: 11px; height: 11px; fill: var(--ink); }
  .address {
    position: absolute; right: 150px; bottom: 26px;
    font-size: 16px; color: var(--ink); line-height: 22px;
  }
  .company-mark {
    position: absolute; right: 12px; top: 138px; width: 130px;
    display: flex; align-items: center; gap: 7px;
    color: var(--card-white); font-weight: 600; font-size: 13px; line-height: 16px;
    text-transform: uppercase; letter-spacing: .4px;
  }
  .company-mark .mark-square {
    flex: none; width: 14px; height: 14px; background: var(--card-white);
  }
  .card-brand { display: flex; align-items: center; justify-content: center; }
  .brand-name {
    display: flex; align-items: center; gap: 16px;
    color: var(--ink); font-weight: 600; font-size: 30px; line-height: 36px;
    text-transform: uppercase; letter-spacing: 1px;
  }
  .brand-name .mark-square { flex: none; width: 34px; height: 34px; background: var(--ink); }
</style>
</head>
<body>
<main class="sheet">
  <section class="card card-contact" aria-label="Business card, contact side">
    <svg class="swoosh" viewBox="0 0 520 300" aria-hidden="true">
      <path d="M240,0 L520,0 L520,262 C420,262 370,220 345,150 C320,80 300,10 240,0 Z" fill="#111"/>
      <path d="M258,0 C318,12 338,84 362,154 C386,222 432,252 520,252" fill="none" stroke="#fff" stroke-width="3"/>
    </svg>

    <div class="holder">
      <p class="holder-name">DANIEL HAYES</p>
      <p class="holder-title">Managing Director</p>
    </div>
    <div class="title-rule"></div>

    <ul class="contact-list">
      <li><svg viewBox="0 0 24 24"><path d="M6.6 10.8a15 15 0 0 0 6.6 6.6l2.2-2.2a1 1 0 0 1 1-.25 11.4 11.4 0 0 0 3.6.57 1 1 0 0 1 1 1V20a1 1 0 0 1-1 1A17 17 0 0 1 3 4a1 1 0 0 1 1-1h3.5a1 1 0 0 1 1 1c0 1.250.2 2.450.57 3.57a1 1 0 0 1-.25 1z"/></svg>123 456 789</li>
      <li><svg viewBox="0 0 24 24"><path d="M2 5h20v14H2zm2 2v.5l8 5 8-5V7zm0 2.8V17h16V9.8l-8 5z"/></svg>info@yourgmail.com</li>
      <li><svg viewBox="0 0 24 24"><path d="M12 2a10 10 0 1 0 0 20 10 10 0 0 0 0-20zm6.9 6h-3a15 15 0 0 0-1.3-3.9A8 8 0 0 1 18.9 8zM12 4a13 13 0 0 1 1.9 4h-3.8A13 13 0 0 1 12 4zM4.3 14a8 8 0 0 1 0-4h3.4a16 16 0 0 0 0 4zm.8 2h3a15 15 0 0 0 1.3 3.9A8 8 0 0 1 5.1 16zm3-8h-3a8 8 0 0 1 4.3-3.9A15 15 0 0 0 8.1 8zM12 20a13 13 0 0 1-1.9-4h3.8A13 13 0 0 1 12 20zm2.3-6H9.7a14 14 0 0 1 0-4h4.6a14 14 0 0 1 0 4zm.3 5.9a15 15 0 0 0 1.3-3.9h3a8 8 0 0 1-4.3 3.9zM16.3 14a16 16 0 0 0 0-4h3.4a8 8 0 0 1 0 4z"/></svg>www.yourwebsite.com</li>
    </ul>

    <p class="address">Your address, City<br>State, Zip 1234</p>

    <div class="company-mark">
      <span class="mark-square"></span>
      <span>Cedar Ridge<br>Mechanical</span>
    </div>
  </section>

  <section class="card card-brand" aria-label="Business card, brand side">
    <div class="brand-name">
      <span class="mark-square"></span>
      <span>Cedar Ridge<br>Mechanical</span>
    </div>
  </section>
</main>
</body>
</html>
```